Modern Business Card For A Digital Advertising Company

I'll be print on the Pell Prints Velour paper http://us.pellprints.com/products/velour/business-cards.html
Need's to be modern and use the color palette of the logo or gray scales. I think integrating the pixelation of the logo in to the card and having it wrap from one side to the other could be interesting. My company provides ad operations, web development, and number of other services to websites around the world. You can see my website at http://www.zantorhq.com
Contact info on the card needs to have
Owen Lasko
President
p.318.204.6637
owen@zantorhq.com
http://www.zantorhq.com
Doesn't necessarily need to be in that order
Website owners
Business

```html
<!DOCTYPE html>
<html lang="en">
<head>
<meta charset="utf-8">
<title>Zantor HQ – Business Card</title>
<link rel="stylesheet" href="https://fonts.googleapis.com/css2?family=Source+Sans+3:wght@400;600;700&display=swap">
<style>
  :root {
    --backdrop: #1c1c1c;
    --card: #ffffff;
    --lime: #8dc63f;
    --ink: #3a3a3a;
    --ink-soft: #5a5a5a;
    --rule: #c9c9c9;
  }
  * { box-sizing: border-box; margin: 0; padding: 0; }
  html, body { width: 1200px; height: 757px; overflow: hidden; }
  body {
    background: var(--backdrop);
    font-family: "Source Sans 3", sans-serif;
    color: var(--ink);
    position: relative;
  }
  .card {
    position: absolute;
    width: 540px;
    height: 308px;
    background: var(--card);
    box-shadow: 0 14px 30px rgba(0,0,0,.55);
  }
  .card--front { left: 60px; top: 110px; }
  .card--back  { left: 600px; top: 340px; }

  .brand {
    position: absolute;
    left: 0; right: 0;
    display: flex;
    align-items: center;
    justify-content: center;
    gap: 12px;
    font-weight: 700;
    color: var(--lime);
    letter-spacing: .04em;
  }
  .brand__square { width: 30px; height: 30px; background: var(--lime); }
  .card--front .brand { top: 78px; font-size: 46px; }

  .identity {
    position: absolute;
    right: 296px;
    top: 218px;
    text-align: right;
  }
  .identity__name { color: var(--lime); font-weight: 600; font-size: 22px; line-height: 1.1; }
  .identity__title { color: var(--ink-soft); font-size: 15px; }

  .divider {
    position: absolute;
    left: 256px; top: 206px;
    width: 1px; height: 72px;
    background: var(--rule);
  }

  .contact {
    position: absolute;
    left: 272px; top: 206px;
    list-style: none;
    font-size: 15px;
    color: var(--ink-soft);
  }
  .contact li { display: flex; align-items: center; gap: 7px; height: 24px; }
  .contact svg { width: 13px; height: 13px; fill: var(--ink); }

  .card--back .brand { top: 56px; font-size: 40px; }
  .services__title {
    position: absolute;
    top: 134px; left: 0; right: 0;
    text-align: center;
    font-weight: 700;
    font-size: 26px;
    letter-spacing: .06em;
  }
  .services__list {
    position: absolute;
    top: 176px; left: 60px; right: 60px;
    list-style: none;
    display: flex;
    flex-wrap: wrap;
    justify-content: center;
    column-gap: 18px;
    row-gap: 2px;
    font-size: 16px;
  }
  .services__list li::before {
    content: "";
    display: inline-block;
    width: 5px; height: 5px;
    background: var(--lime);
    margin-right: 6px;
    vertical-align: middle;
  }
  .services__break { flex-basis: 100%; height: 0; }
  .services__break::before { display: none !important; }
</style>
</head>
<body>

  <section class="card card--front" aria-label="Card front">
    <div class="brand"><span class="brand__square"></span><span>ZANTOR HQ</span></div>

    <div class="identity">
      <p class="identity__name">Owen Lasko</p>
      <p class="identity__title">President</p>
    </div>

    <div class="divider"></div>

    <ul class="contact">
      <li>
        <svg viewBox="0 0 16 16" aria-hidden="true"><path d="M3.6 1.2 6 3.8 4.6 5.6c.9 2.2 3.6 4.9 5.8 5.8l1.8-1.4 2.6 2.4-1.6 2.2C7.4 14.4 1.6 8.6 1.4 2.8z"/></svg>
        <span>318.204.6637</span>
      </li>
      <li>
        <svg viewBox="0 0 16 16" aria-hidden="true"><path d="M1 3h14v10H1zM2.4 4.2 8 8.6l5.6-4.4z" fill-rule="evenodd"/></svg>
        <span>owen@zantorhq.com</span>
      </li>
      <li>
        <svg viewBox="0 0 16 16" aria-hidden="true"><circle cx="8" cy="8" r="7"/><path d="M1 8h14M8 1c-3 3.5-3 10.5 0 14M8 1c3 3.5 3 10.5 0 14" stroke="#fff" stroke-width="1" fill="none"/></svg>
        <span>www.zantorhq.com</span>
      </li>
    </ul>
  </section>

  <section class="card card--back" aria-label="Card back">
    <div class="brand"><span class="brand__square"></span><span>ZANTOR HQ</span></div>

    <h2 class="services__title">Services</h2>
    <ul class="services__list">
      <li>Ad Operations</li>
      <li>Web Development</li>
      <li class="services__break"></li>
      <li>Hosting</li>
      <li>Site Speed</li>
      <li class="services__break"></li>
      <li>Social Media</li>
      <li class="services__break"></li>
      <li>Search Engine Optimization</li>
    </ul>
  </section>

</body>
</html>
```